Business Cards Design for the electrical wholesaler: clean bold dynamic :)

We need a business card design that would follow our latest brand guidelines. As an electrical wholesaler we want to bring a fresh look and feel into the industry. The design should be clean bold and dynamic. It should come alive with the renewed energy of our green colour. Our grey colour should keep things balanced and complement the notion of maturity and responsibility. We employ Lato as a corporate font however are not bound by this font and we’re open to interpretation here.

Target Market(s)

Electrical contractors

Industry/Entity Type

Business

Contact Information for Business Card

Logo
Name & Surname: Halyna Dorosh
Job Title: Director of Marketing
Email: halya.dorosh@quillmail.example
Cell phone: XXX.XXX.XXXX
Address: 20517 - 87 Ave. Edmonton, AB, Canada. T6K 4N8
Business Phone: 780.555.0184
Website: www.brovix.example

Font styles to use
Other font styles liked:
• Lato

Requirements
Must have
• Logo & website
Nice to have
• Brand elements - some of them you may find in the attached Brand Guidelines (e.g. three lines on the background signifying "W")

```html
<!DOCTYPE html>
<html lang="en">
<head>
<meta charset="utf-8">
<title>Brovix Business Cards</title>
<link rel="stylesheet" href="https://fonts.googleapis.com/css2?family=Lato:wght@400;700&display=swap">
<style>
  :root {
    --bg: #eceef0;
    --card: #ffffff;
    --ink: #4a4a4c;
    --ink-soft: #6b6b6d;
    --green: #8dc63f;
    --mark-tone: #e4e4e4;
    --rule: #6b6b6d;
  }
  * { margin: 0; padding: 0; box-sizing: border-box; }
  html, body { width: 1200px; height: 1000px; overflow: hidden; }
  body {
    background: var(--bg);
    font-family: "Lato", sans-serif;
    color: var(--ink);
    position: relative;
  }
  .card {
    position: absolute;
    background: var(--card);
    overflow: hidden;
    box-shadow: 0 4px 14px rgba(0,0,0,0.12);
  }
  .card--rounded { border-radius: 28px; }
  .card--front-a { left: 64px; top: 60px; width: 508px; height: 290px; }
  .card--back-a  { left: 64px; top: 428px; width: 508px; height: 288px; }
  .card--front-b { left: 624px; top: 283px; width: 514px; height: 292px; }
  .card--back-b  { left: 624px; top: 639px; width: 514px; height: 292px; }

  .brand-decor {
    position: absolute; left: 0; top: 28px; width: 240px; height: 230px;
    background: linear-gradient(120deg, var(--mark-tone), #f1f1f1);
  }
  .brand {
    position: absolute; display: flex; align-items: center; gap: 10px;
  }
  .brand__square { width: 26px; height: 26px; background: var(--green); }
  .brand__name { font-weight: 700; font-size: 40px; line-height: 1; color: var(--ink); letter-spacing: -0.5px; }
  .card__front .brand { right: 46px; top: 126px; }
  .card__back .brand { right: 30px; top: 24px; }

  .person { position: absolute; left: 27px; top: 82px; }
  .person__name { font-size: 26px; font-weight: 400; line-height: 1.1; }
  .person__title { font-size: 15px; color: var(--ink-soft); margin-top: 3px; }
  .divider { position: absolute; left: 27px; right: 30px; top: 142px; height: 1.5px; background: var(--rule); }
  .address {
    position: absolute; right: 30px; top: 146px; text-align: right;
    font-size: 15px; line-height: 18px; color: var(--ink-soft);
  }
  .address__line { display: flex; align-items: center; justify-content: flex-end; gap: 8px; }
  .contacts { position: absolute; left: 27px; top: 176px; list-style: none; }
  .contacts li { display: flex; align-items: center; gap: 10px; font-size: 17px; line-height: 24px; }
  .icon { width: 14px; height: 14px; fill: var(--ink); flex: none; }
  .website { position: absolute; right: 30px; bottom: 24px; font-size: 15px; color: var(--ink-soft); }
</style>
</head>
<body>

  <!-- Rounded variant: front -->
  <section class="card card--rounded card--front-a card__front">
    <div class="brand-decor" role="img" aria-label="Faint large brand decoration"></div>
    <div class="brand"><span class="brand__square"></span><span class="brand__name">brovix</span></div>
  </section>

  <!-- Rounded variant: back -->
  <section class="card card--rounded card--back-a card__back">
    <div class="brand"><span class="brand__square"></span><span class="brand__name">brovix</span></div>
    <div class="person">
      <h1 class="person__name">Halyna Dorosh</h1>
      <p class="person__title">Director of Marketing</p>
    </div>
    <div class="divider"></div>
    <div class="address">
      <div class="address__line">
        <svg class="icon" viewBox="0 0 24 24"><path d="M12 2a7 7 0 0 0-7 7c0 5 7 13 7 13s7-8 7-13a7 7 0 0 0-7-7zm0 9.5A2.5 2.5 0 1 1 12 6.5a2.5 2.5 0 0 1 0 5z"/></svg>
        <span>20517 - 87 Ave. Edmonton</span>
      </div>
      <div>AB, Canada. T6K 4N8</div>
    </div>
    <ul class="contacts">
      <li><svg class="icon" viewBox="0 0 24 24"><path d="M6.6 10.8a15 15 0 0 0 6.6 6.6l2.2-2.2a1 1 0 0 1 1-.25 11.4 11.4 0 0 0 3.6.57 1 1 0 0 1 1 1V20a1 1 0 0 1-1 1A17 17 0 0 1 3 4a1 1 0 0 1 1-1h3.5a1 1 0 0 1 1 1c0 1.25.2 2.45.57 3.57a1 1 0 0 1-.25 1z"/></svg>780.555.0184</li>
      <li><svg class="icon" viewBox="0 0 24 24"><path d="M2 9c3-4 17-4 20 0l-3 2-3-2V7.5c-2.5-.7-5.5-.7-8 0V9l-3 2zM6 13h12l2 7H4z"/></svg>780.555.0184</li>
      <li><svg class="icon" viewBox="0 0 24 24"><path d="M2 5h20v14H2zm2 2v.5l8 5 8-5V7z"/></svg>halya.dorosh@quillmail.example</li>
    </ul>
    <p class="website">www.brovix.example</p>
  </section>

  <!-- Square variant: front -->
  <section class="card card--front-b card__front">
    <div class="brand-decor" role="img" aria-label="Faint large brand decoration"></div>
    <div class="brand"><span class="brand__square"></span><span class="brand__name">brovix</span></div>
  </section>

  <!-- Square variant: back -->
  <section class="card card--back-b card__back">
    <div class="brand"><span class="brand__square"></span><span class="brand__name">brovix</span></div>
    <div class="person">
      <h2 class="person__name">Halyna Dorosh</h2>
      <p class="person__title">Director of Marketing</p>
    </div>
    <div class="divider"></div>
    <div class="address">
      <div class="address__line">
        <svg class="icon" viewBox="0 0 24 24"><path d="M12 2a7 7 0 0 0-7 7c0 5 7 13 7 13s7-8 7-13a7 7 0 0 0-7-7zm0 9.5A2.5 2.5 0 1 1 12 6.5a2.5 2.5 0 0 1 0 5z"/></svg>
        <span>20517 - 87 Ave. Edmonton</span>
      </div>
      <div>AB, Canada. T6K 4N8</div>
    </div>
    <ul class="contacts">
      <li><svg class="icon" viewBox="0 0 24 24"><path d="M6.6 10.8a15 15 0 0 0 6.6 6.6l2.2-2.2a1 1 0 0 1 1-.25 11.4 11.4 0 0 0 3.6.57 1 1 0 0 1 1 1V20a1 1 0 0 1-1 1A17 17 0 0 1 3 4a1 1 0 0 1 1-1h3.5a1 1 0 0 1 1 1c0 1.25.2 2.45.57 3.57a1 1 0 0 1-.25 1z"/></svg>780.555.0184</li>
      <li><svg class="icon" viewBox="0 0 24 24"><path d="M2 9c3-4 17-4 20 0l-3 2-3-2V7.5c-2.5-.7-5.5-.7-8 0V9l-3 2zM6 13h12l2 7H4z"/></svg>780.555.0184</li>
      <li><svg class="icon" viewBox="0 0 24 24"><path d="M2 5h20v14H2zm2 2v.5l8 5 8-5V7z"/></svg>halya.dorosh@quillmail.example</li>
    </ul>
    <p class="website">www.brovix.example</p>
  </section>

</body>
</html>
```